Business Cards for company that supports physicians that do medical research

Need to create a business card for Qorvel Studies (www.qorvelstudies.example), a company devoted to supporting physicians who conduct medical research. The form of the card should match the message of research and information quest. I have provided the logo of the company as an uploaded file. Designs should be simple and slick aimed at very high end clients.

Target Market(s)

Medical doctors that are also researchers

Industry/Entity Type

Medical

Contact Information for Business Card

Should feature logo and fields for personal info:
Name/title
Phone /email

Font styles to use
Serif
Sans Serif

Requirements
Must have
• Qorvel logo and fields for personal info:
• Name: Bertrand Okonfu
• Title: VP Research and Senior Analyst
• Phone: 555-203-4719
• email: info@qorvelstudies.example
Nice to have
• Interesting cards that I've seen:
• 1- all black/charcoal or very dark background
• 2- Plastic - semi-transparent
• 3- non-standard height-width ratios
• 4- Functional cards -- USB drive incorporated
Should not have
• Too busy; needs to stay very simple

```html
<!DOCTYPE html>
<html lang="en">
<head>
<meta charset="utf-8">
<title>Qorvel Studies – Business Cards</title>
<link href="https://fonts.googleapis.com/css2?family=Open+Sans:wght@400;600;700&display=swap" rel="stylesheet">
<style>
  :root {
    --backdrop: #2c2e32;
    --brand-green: #5cbf45;
    --brand-green-light: #6cc653;
    --card-black: #050505;
    --text-white: #ffffff;
    --icon-green: #5cbf45;
  }
  * { box-sizing: border-box; margin: 0; padding: 0; }
  html, body {
    width: 1200px;
    height: 864px;
    overflow: hidden;
    background: var(--backdrop);
    font-family: "Open Sans", Arial, sans-serif;
  }
  .sheet {
    position: relative;
    width: 1200px;
    height: 864px;
  }
  .card {
    position: absolute;
    width: 600px;
    height: 343px;
    border-radius: 4px;
    box-shadow: 0 14px 30px rgba(0, 0, 0, 0.45);
  }
  .card--front {
    left: 300px;
    top: 60px;
    background: linear-gradient(160deg, var(--brand-green-light), var(--brand-green));
    display: flex;
    align-items: center;
    justify-content: center;
  }
  .card--back {
    left: 300px;
    top: 450px;
    background: var(--card-black);
    color: var(--text-white);
  }
  .wordmark {
    font-weight: 700;
    letter-spacing: 1px;
    white-space: nowrap;
  }
  .card--front .wordmark {
    color: var(--text-white);
    font-size: 52px;
  }
  .card--back .wordmark {
    position: absolute;
    left: 0;
    right: 0;
    top: 62px;
    text-align: center;
    color: var(--brand-green);
    font-size: 46px;
  }
  .holder {
    position: absolute;
    left: 34px;
    top: 222px;
  }
  .holder__name {
    color: var(--brand-green);
    font-weight: 700;
    font-size: 19px;
    margin-bottom: 8px;
  }
  .holder__title {
    font-size: 14px;
  }
  .contact {
    position: absolute;
    right: 24px;
    top: 262px;
    list-style: none;
    text-align: right;
    font-size: 14px;
  }
  .contact__item {
    display: flex;
    align-items: center;
    justify-content: flex-end;
    gap: 8px;
    height: 22px;
  }
  .contact__icon {
    width: 18px;
    height: 15px;
    flex: none;
  }
</style>
</head>
<body>
  <main class="sheet">
    <section class="card card--front" aria-label="Card front">
      <p class="wordmark">Qorvel Studies</p>
    </section>

    <section class="card card--back" aria-label="Card back">
      <p class="wordmark">Qorvel Studies</p>

      <div class="holder">
        <p class="holder__name">Bertrand Okonfu</p>
        <p class="holder__title">VP Research and Senior Analyst</p>
      </div>

      <ul class="contact">
        <li class="contact__item">
          <span>555-203-4719</span>
          <svg class="contact__icon" viewBox="0 0 18 15" aria-hidden="true">
            <rect width="18" height="15" rx="2" fill="var(--icon-green)"/>
            <path d="M4 6 Q9 2 14 6 L12.5 7.5 Q9 5.5 5.5 7.5 Z" fill="#fff"/>
            <rect x="5.5" y="8" width="7" height="4" rx="1" fill="#fff"/>
          </svg>
        </li>
        <li class="contact__item">
          <span>info@qorvelstudies.example</span>
          <svg class="contact__icon" viewBox="0 0 18 15" aria-hidden="true">
            <rect width="18" height="15" rx="2" fill="var(--icon-green)"/>
            <rect x="4" y="4" width="10" height="7" fill="#fff"/>
            <path d="M4 4 L9 8 L14 4" fill="none" stroke="var(--icon-green)" stroke-width="1"/>
          </svg>
        </li>
      </ul>
    </section>
  </main>
</body>
</html>
```